Business Card Design

Electronic Security Installation Specialists

Check out our website at www.tallbrookllc.com to see what we do.

Industry/Entity Type

Business

Contact Information for Business Card

Tall Brook
Marjorie Hadley
281 Orchard Rise
Mapleton, WV 25871

Colors
3176b5
0455a3
ffffff

```html
<!DOCTYPE html>
<html lang="en">
<head>
<meta charset="utf-8">
<title>Tall Brook – Business Card</title>
<link rel="stylesheet" href="https://fonts.googleapis.com/css2?family=Open+Sans:wght@400;600;700&display=swap">
<style>
  :root {
    --blue-light: #3176b5;
    --blue-mid: #1f6fb8;
    --blue-deep: #0455a3;
    --blue-night: #033f80;
    --white: #ffffff;
    --text-soft: #d8e8f7;
    --backdrop: #e9ecef;
  }
  * { box-sizing: border-box; margin: 0; padding: 0; }
  html, body { width: 1200px; height: 913px; overflow: hidden; }
  body {
    background: var(--backdrop);
    font-family: "Open Sans", Arial, sans-serif;
    position: relative;
  }
  .card {
    position: absolute;
    top: 306px;
    width: 525px;
    height: 300px;
    border-radius: 4px;
    overflow: hidden;
    background: linear-gradient(160deg, var(--blue-mid) 0%, var(--blue-deep) 55%, var(--blue-night) 100%);
    box-shadow: 0 6px 18px rgba(0, 0, 0, 0.18);
  }
  .card--front { left: 50px; }
  .card--back { left: 625px; }

  .cable-decor {
    position: absolute;
    height: 34px;
    border-radius: 17px;
    background: linear-gradient(90deg, rgba(255,255,255,0), rgba(255,255,255,0.16), rgba(255,255,255,0));
  }
  .card--front .cable-decor--top { left: 250px; top: 26px; width: 190px; }
  .card--front .cable-decor--bottom { left: 30px; top: 236px; width: 190px; }
  .card--back .cable-decor--top { left: 330px; top: 20px; width: 170px; }

  .brand-badge {
    position: absolute;
    width: 196px;
    height: 160px;
    border-radius: 50%;
    background: var(--white);
    border: 3px solid var(--white);
    display: flex;
    align-items: center;
    justify-content: center;
  }
  .card--front .brand-badge { left: 164px; top: 70px; }
  .card--back .brand-badge { left: 40px; top: 90px; width: 170px; height: 140px; }
  .brand-name {
    font-weight: 700;
    font-size: 30px;
    color: var(--blue-deep);
    letter-spacing: 0.5px;
  }
  .card--back .brand-name { font-size: 26px; }

  .contact {
    position: absolute;
    left: 262px;
    top: 62px;
    color: var(--white);
  }
  .contact__name { font-weight: 700; font-size: 15px; }
  .contact__title { font-size: 10.5px; color: var(--text-soft); margin-top: 1px; }
  .contact__list { list-style: none; margin-top: 30px; }
  .contact__item {
    display: flex;
    align-items: flex-start;
    gap: 8px;
    font-size: 11px;
    line-height: 15px;
    color: var(--text-soft);
  }
  .contact__item svg { width: 10px; height: 10px; margin-top: 3px; flex: none; fill: var(--white); }
</style>
</head>
<body>
  <section class="card card--front" aria-label="Business card front">
    <div class="cable-decor cable-decor--top" role="img" aria-label="Faint cable illustration"></div>
    <div class="cable-decor cable-decor--bottom" role="img" aria-label="Faint cable illustration"></div>
    <div class="brand-badge"><span class="brand-name">Tall Brook</span></div>
  </section>

  <section class="card card--back" aria-label="Business card back">
    <div class="cable-decor cable-decor--top" role="img" aria-label="Faint cable illustration"></div>
    <div class="brand-badge"><span class="brand-name">Tall Brook</span></div>
    <div class="contact">
      <p class="contact__name">Marjorie Hadley</p>
      <p class="contact__title">Managing Director</p>
      <ul class="contact__list">
        <li class="contact__item">
          <svg viewBox="0 0 10 10" aria-hidden="true"><path d="M1 1h3l1 2-1.5 1a6 6 0 0 0 2.5 2.5L7 5l2 1v3C4 9 1 6 1 1z"/></svg>
          <span>301-555-0148</span>
        </li>
        <li class="contact__item">
          <svg viewBox="0 0 10 10" aria-hidden="true"><path d="M0 2h10v6H0z M0 2l5 3.5L10 2" stroke="#0455a3" stroke-width="0.8"/></svg>
          <span>m.hadley@tallbrookllc.com</span>
        </li>
        <li class="contact__item">
          <svg viewBox="0 0 10 10" aria-hidden="true"><circle cx="5" cy="5" r="4.5"/></svg>
          <span>www.tallbrookllc.com</span>
        </li>
        <li class="contact__item">
          <svg viewBox="0 0 10 10" aria-hidden="true"><path d="M5 0a3.5 3.5 0 0 1 3.5 3.5C8.5 6 5 10 5 10S1.5 6 1.5 3.5A3.5 3.5 0 0 1 5 0z"/></svg>
          <span>281 Orchard Rise<br>Mapleton, WV 25871</span>
        </li>
      </ul>
    </div>
  </section>
</body>
</html>
```